Marine Services Letterhead design

We need a letterhead design for an Australian owned company in Victoria named K+T Harbour Works Pty Ltd. We provide linesmen and launches to assist the large ships that come into port.
Our colour is orange.
The final design should have a strong nautical theme and communicate safety and reliability.
I would like to use the letter head on invoices so it should print to pdf well.

Target Market(s)

Owners and representatives of shipping companies. It is not for general public

Industry/Entity Type

Nautical

Requirements
Must have
• A shipping theme, not overly complicated, featuring safety orange colours but not all orange of course.
The letterhead should just sit at the top of the page so I can use for invoices.
Nice to have
• Something elegant and stylish
Should not have
• cartoons or pop art

```html
<!DOCTYPE html>
<html lang="en">
<head>
<meta charset="utf-8">
<title>K+T Harbour Works Pty Ltd — Letterhead</title>
<link rel="stylesheet" href="https://fonts.googleapis.com/css2?family=Source+Sans+3:wght@400;700&display=swap">
<style>
  :root {
    --paper: #ffffff;
    --ink: #231f20;
    --band: #b0692a;
    --band-text: #ffffff;
    --mark: #d9893a;
    --rule: #111111;
  }
  * { margin: 0; padding: 0; box-sizing: border-box; }
  html, body { width: 946px; height: 1200px; overflow: hidden; background: var(--paper); }
  .letterhead {
    position: relative;
    width: 946px;
    height: 1200px;
    background: var(--paper);
    font-family: "Source Sans 3", "Myriad Pro", Arial, sans-serif;
    color: var(--ink);
  }
  .brand {
    position: absolute;
    top: 60px;
    left: 0;
    width: 100%;
    display: flex;
    flex-direction: column;
    align-items: center;
    gap: 22px;
  }
  .brand-dot {
    width: 130px;
    height: 130px;
    border-radius: 50%;
    background: var(--mark);
  }
  .brand-name {
    font-size: 21px;
    font-weight: 700;
    letter-spacing: 0.1px;
    color: var(--ink);
  }
  .footer-wave {
    position: absolute;
    left: 0;
    top: 0;
    width: 946px;
    height: 1200px;
  }
  .contact {
    position: absolute;
    left: 0;
    width: 100%;
    text-align: center;
    color: var(--band-text);
  }
  .contact-address {
    top: 1134px;
    font-size: 17px;
    letter-spacing: 2px;
  }
  .contact-line {
    top: 1166px;
    font-size: 15.5px;
    display: flex;
    justify-content: center;
    align-items: center;
    gap: 10px;
  }
  .contact-divider {
    width: 1px;
    height: 24px;
    background: var(--band-text);
  }
  .icon { display: inline-block; vertical-align: -2px; margin-right: 4px; }
</style>
</head>
<body>
<div class="letterhead">
  <header class="brand">
    <div class="brand-dot"></div>
    <div class="brand-name">K+T Harbour Works Pty Ltd</div>
  </header>

  <svg class="footer-wave" viewBox="0 0 946 1200" aria-hidden="true">
    <path d="M0,1166 Q473,1034 946,1166 L946,1200 L0,1200 Z" fill="var(--rule)"/>
    <path d="M0,1169 Q473,1046 946,1169 L946,1200 L0,1200 Z" fill="var(--paper)"/>
    <path d="M0,1172 Q473,1050 946,1172 L946,1200 L0,1200 Z" fill="var(--band)"/>
  </svg>

  <footer>
    <div class="contact contact-address">
      <svg class="icon" width="11" height="16" viewBox="0 0 11 16"><path d="M5.5 0C2.5 0 0 2.4 0 5.4 0 9.5 5.5 16 5.5 16S11 9.5 11 5.4C11 2.4 8.5 0 5.5 0Zm0 7.6a2.2 2.2 0 1 1 0-4.4 2.2 2.2 0 0 1 0 4.4Z" fill="#fff"/></svg>PO Box 214 Seaview 3940
    </div>
    <div class="contact contact-line">
      <span><svg class="icon" width="14" height="14" viewBox="0 0 24 24"><path d="M6.6 10.8a15.1 15.1 0 0 0 6.6 6.6l2.2-2.2c.3-.3.7-.4 1-.2 1.1.4 2.3.6 3.6.6.6 0 1 .4 1 1V20c0 .6-.4 1-1 1A17 17 0 0 1 3 4c0-.6.4-1 1-1h3.5c.6 0 1 .4 1 1 0 1.3.2 2.5.6 3.6.1.3 0 .7-.2 1Z" fill="none" stroke="#fff" stroke-width="2"/></svg>1300 555 017</span>
      <span class="contact-divider"></span>
      <span>ABN: 12345678901</span>
    </div>
  </footer>
</div>
</body>
</html>
```